Brenwick Structures Construction Company Seeking Modern Website

We are a small construction company wanting to create a web presence. We don't have much in the way of current content but will get photos as they come in. Attached is a picture of our business card.
The pages we would like on the menu are:
Home
Portfolio
Product Specs
Testimonials
Our Process
Contact
Some designs we like are:
http://www.tovasheds-example.com/
http://www.qrnstructures-example.com/
http://dunholtbarns-example.com/
http://pellingframes-example.com/
Not much requirements other than that so feel free to be creative!
Updates
Target Market(s)
Construction
Commercial and Residential Buildings
Industry/Entity Type
Construction Company
Number of Pages Required
5+ page
Look and feel

```html
<!DOCTYPE html>
<html lang="en">
<head>
<meta charset="utf-8">
<title>Brenwick Structures</title>
<link href="https://fonts.googleapis.com/css2?family=Roboto:wght@300;400;500&display=swap" rel="stylesheet">
<style>
:root{
  --red:#d9302a;
  --blue:#1e9ad6;
  --text:#555;
  --muted:#888;
  --line:#d8d8d8;
  --band:#ececec;
  --footer:#262626;
  --footer-text:#a8a8a8;
}
*{box-sizing:border-box;margin:0;padding:0}
html,body{width:1141px;height:1200px;overflow:hidden;background:#fff;font-family:'Roboto',sans-serif;color:var(--text)}
.page{position:relative;width:1141px;height:1200px}
.abs{position:absolute}
.brand{left:95px;top:36px;font-size:30px;font-weight:500;color:var(--red);display:flex;align-items:center;gap:10px}
.brand .mark{width:22px;height:22px;background:var(--red)}
.call{left:694px;top:30px;font-size:14px;color:var(--muted);display:flex;align-items:center;gap:5px}
.call b{font-weight:400;color:var(--blue)}
.search{left:885px;top:24px;width:161px;height:29px;border:1px solid var(--line);font-size:10px;color:var(--muted);padding:8px 9px}
.search svg{position:absolute;right:9px;top:8px}
.nav{right:95px;top:71px;display:flex;gap:34px;font-size:12px;color:#666}
.nav .active{color:var(--red)}
.hero-band{left:0;top:110px;width:1141px;height:399px;background:var(--band)}
.hero{left:93px;top:110px;width:953px;height:399px;background:linear-gradient(180deg,#8a96c8 0%,#b7b9d6 35%,#8a7f78 65%,#6f6a55 100%)}
.arrow{top:293px;width:25px;height:33px;background:rgba(90,90,90,.7)}
.feature{top:553px;width:450px}
.feature .ph{position:absolute;left:0;top:0;width:209px;height:189px}
.feature h2{position:absolute;left:225px;top:0;font-size:20px;font-weight:400;color:var(--red);white-space:nowrap}
.feature p{position:absolute;left:225px;top:32px;width:225px;font-size:10.5px;line-height:18px;color:var(--muted);font-weight:300}
.feature a{position:absolute;left:225px;top:180px;font-size:10.5px;color:#222;text-decoration:none}
.rule{left:94px;width:952px;height:1px;background:var(--line)}
.quote-icon{left:548px;top:791px;width:45px;height:44px;background:#d6d6d6;display:flex;align-items:center;justify-content:center}
.quote{left:160px;top:856px;width:821px;text-align:center;font-size:13px;line-height:24.5px;color:#777;font-weight:300}
.author{left:0;top:943px;width:1141px;text-align:center;font-size:12.5px;color:#222}
.dots{left:513px;top:983px;width:115px;height:28px;background:#d6d6d6;display:flex;align-items:center;justify-content:center;gap:15px}
.dots span{width:9px;height:9px;border-radius:50%;background:#fff}
.dots span.on{background:#fff;box-shadow:inset 0 0 0 2px #fff,inset 0 0 0 5px #999}
.contacts{top:1053px;font-size:11.5px;color:#666;display:flex;align-items:center;gap:7px}
.footer{left:0;top:1102px;width:1141px;height:98px;background:var(--footer)}
.flinks{left:95px;top:1131px;font-size:10.5px;color:var(--footer-text);word-spacing:2px}
.copy{left:95px;top:1157px;font-size:10.5px;color:var(--footer-text)}
.social{left:949px;top:1139px;display:flex;gap:10px}
.social span{width:25px;height:25px;border-radius:50%}
</style>
</head>
<body>
<div class="page">
  <div class="abs brand"><span class="mark"></span>Brenwick Structures</div>
  <div class="abs call">
    <svg width="10" height="10" viewBox="0 0 24 24"><path fill="#999" d="M6.6 10.8a15 15 0 006.6 6.6l2.2-2.2c.3-.3.7-.4 1-.2 1.1.4 2.3.6 3.6.6.6 0 1 .4 1 1V20c0 .6-.4 1-1 1A17 17 0 013 4c0-.6.4-1 1-1h3.5c.6 0 1 .4 1 1 0 1.3.2 2.5.6 3.6.1.3 0 .7-.2 1z"/></svg>
    Call us on : <b>555 014 2290</b>
  </div>
  <div class="abs search">Search
    <svg width="12" height="12" viewBox="0 0 24 24"><circle cx="10" cy="10" r="7" fill="none" stroke="#1e9ad6" stroke-width="3"/><path d="M15 15l6 6" stroke="#1e9ad6" stroke-width="3"/></svg>
  </div>
  <nav class="abs nav">
    <span class="active">Home</span><span>Portfolio</span><span>Product Specs</span><span>Testimonials</span><span>Our Process</span><span>Contact</span>
  </nav>

  <div class="abs hero-band"></div>
  <div class="abs hero" role="img" aria-label="Two-storey family home with lit windows and double garage at dusk"></div>
  <div class="abs arrow" style="left:93px"><svg width="25" height="33"><path d="M16 8l-7 8.5 7 8.5" fill="none" stroke="#fff" stroke-width="1.5"/></svg></div>
  <div class="abs arrow" style="left:1021px"><svg width="25" height="33"><path d="M9 8l7 8.5-7 8.5" fill="none" stroke="#fff" stroke-width="1.5"/></svg></div>

  <section class="abs feature" style="left:94px">
    <div class="ph" role="img" aria-label="Modern white office building with glass facade under blue sky" style="background:linear-gradient(180deg,#4f7fc4 0%,#a9c3df 45%,#d9dde0 70%,#6f9a3e 100%)"></div>
    <h2>Commercial Construction</h2>
    <p>Aenean faucibus lacus ut mollis commodo. Donec vestibulum odio sem, ac laoreet massa ullamcorper id. Donec molestie nisi et tellus hendrerit vehicula. Nunc eu ligula sed quam pulvinar maximus in vitae eros. Proin porta fermentum ipsum, vel porttitor turpis venenatis luctus. Aenean feugiat viverra lorem.</p>
    <a href="#">READ MORE</a>
  </section>
  <section class="abs feature" style="left:600px">
    <div class="ph" role="img" aria-label="Cream two-storey house with stone garden wall and lawn" style="background:linear-gradient(180deg,#6f9fd8 0%,#d9d0b0 40%,#c9a872 65%,#4f8a34 100%)"></div>
    <h2>Residential Buildings</h2>
    <p>Aenean faucibus lacus ut mollis commodo. Donec vestibulum odio sem, ac laoreet massa ullamcorper id. Donec molestie nisi et tellus hendrerit vehicula. Nunc eu ligula sed quam pulvinar maximus in vitae eros. Proin porta fermentum ipsum, vel porttitor turpis venenatis luctus. Aenean feugiat viverra lorem.</p>
    <a href="#">READ MORE</a>
  </section>

  <div class="abs rule" style="top:791px"></div>
  <div class="abs quote-icon">
    <svg width="18" height="14" viewBox="0 0 18 14"><path fill="#fff" d="M0 14V8C0 3 2.5.5 7 0v3C4.5 3.5 3.5 5 3.5 7H7v7zm10 0V8c0-5 2.5-7.5 7-8v3c-2.5.5-3.5 2-3.5 4H17v7z"/></svg>
  </div>
  <p class="abs quote">“ Nam fringilla nulla vel nisl condimentum, dapibus condimentum enim porta. Phasellus blandit quam a ipsum gravida dapibus. Cras sed augue tortor. Suspendisse elit ligula, iaculis dignissim justo eu, vestibulum venenatis elit. Sed egestas, nisl id cursus ultricies, turpis orci rhoncus odio, id tristique odio ex in lacus. Nam suscipit sapien eget blandit sollicitudin. ”</p>
  <div class="abs author">Marcus Hale, City</div>
  <div class="abs dots"><span class="on"></span><span></span><span></span><span></span></div>
  <div class="abs rule" style="top:1011px"></div>

  <div class="abs contacts" style="left:103px">
    <svg width="8" height="11" viewBox="0 0 16 22"><path fill="#777" d="M8 0a8 8 0 00-8 8c0 6 8 14 8 14s8-8 8-14a8 8 0 00-8-8zm0 11a3 3 0 110-6 3 3 0 010 6z"/></svg>
    24 Building name, Street name, City - Zipcode
  </div>
  <div class="abs contacts" style="left:437px">
    <svg width="10" height="10" viewBox="0 0 24 24"><path fill="#777" d="M6.6 10.8a15 15 0 006.6 6.6l2.2-2.2c.3-.3.7-.4 1-.2 1.1.4 2.3.6 3.6.6.6 0 1 .4 1 1V20c0 .6-.4 1-1 1A17 17 0 013 4c0-.6.4-1 1-1h3.5c.6 0 1 .4 1 1 0 1.3.2 2.5.6 3.6.1.3 0 .7-.2 1z"/></svg>
    Phone: 555 018 4471
  </div>
  <div class="abs contacts" style="left:650px">
    <svg width="12" height="11" viewBox="0 0 24 22"><rect x="0" y="6" width="24" height="16" rx="2" fill="#777"/><rect x="6" y="0" width="12" height="8" fill="#777"/><rect x="4" y="11" width="16" height="2" fill="#fff"/><rect x="4" y="15" width="16" height="2" fill="#fff"/></svg>
    Fax: 555 016 3902
  </div>
  <div class="abs contacts" style="left:851px">
    <svg width="12" height="9" viewBox="0 0 24 18"><rect width="24" height="18" rx="2" fill="#777"/><path d="M1 2l11 8 11-8" fill="none" stroke="#fff" stroke-width="2"/></svg>
    E-mail : info@brenwick-example.com
  </div>

  <footer class="abs footer"></footer>
  <div class="abs flinks">Home &nbsp;|&nbsp; Portfolio &nbsp;|&nbsp; Product Specs &nbsp;|&nbsp; Testimonials &nbsp;|&nbsp; Our Process &nbsp;|&nbsp; Contact</div>
  <div class="abs copy">Copyright © 2015 &nbsp;Ardent Pile Works. All rights reserved</div>
  <div class="abs social">
    <span style="background:#3b5ba0"></span><span style="background:#2aa8e0"></span><span style="background:#1d86b8"></span>
  </div>
</div>
</body>
</html>
```